Sharpen Your Calling book cover and updated company logo bundle

USE THE LOGO ON THE BACK COVER. I WANT AN UPDATED LOOK TO MY LOGO
Size of book: 5.5 x 8.5
Title: Sharpen Your Calling
Subtitle: A quiet person’s handbook for building a mentoring practice that mirrors your true self
The Subtitle does NOT go on the book cover
Author: Norah Baltimer
BOOK DESCRIPTION: This book will help coaches and creative professionals get confidently clear on who they are so they can create a business that reflects their inner message.

DEMOGRAPHICS — Coaches and creative professional age 35-45

WOULD YOU PREFER PEOPLE OR OBJECTS ON YOUR COVER?
Objects or abstract designs
Anything I don’t want on the cover? people
Objects or symbols I want on the cover: possibly magnifying glass

IF YOU HAVE ANY PHOTOS THAT YOU WOULD LIKE US TO USE, PLEASE INCLUDE THE LINK(S) HERE. My logo or face pic for the back cover (Face pic pending)

COPY FOR THE SPINE
Sharpen Your Calling
Norah Baltimer
Lanternfield Books (with logo)

COPY FOR THE BACK COVER (270 words) my biz logo at the bottom and my picture next to my short bio. (Picture to come)

Build a Mentoring Practice that Mirrors Your True Self

Do you want to step confidently into your new career by doing what you love? You aren't alone! But instead of doing what they love, many new coaches get stuck by trying to fit into traditional ways of doing business and create many unnecessary hurdles to happiness and success.
In this book, creative business coach, Norah Baltimer teaches you, as she has taught herself and many others, to stop feeling guilty about what you “should” do in your life and in the process you will learn how to turn your passion into a purposeful career.

New coaches will learn how to:
• Recognize how your life decisions to this point are holding you back.
• Discover your gifts so you can express yourself through your creative projects.
• Identify and develop tools to bring your passion into purpose
• Offer services based on what you love to do.
• Understand your personal work style and work-flow to optimize your ideas and productivity.
• Create a message that reflects who you are to attract clients to work with you.
• Ask confidently for what you are worth and get it every time.
Join Norah on the journey of reconnecting with yourself and manifesting your dream.

Norah Baltimer, founder of Quiet Harbor Wellness, helps new coaches and creative entrepreneurs find their inner voice so that they have the confidence to bring their authentic selves out into the world. Norah has gone through this process for herself and helped other new businesses achieve dramatic improvements in their organization and focus as a result.

Target Market(s)

indicated in description

Industry/Entity Type

Life Coaching

Logo Text

Quiet Harbor Wellness

Requirements
Must have
• updated look on existing logo it is going on the back of the book
Nice to have
• I like the font in the book cover I attached but Id like to see what else is possible

```html
<!DOCTYPE html>
<html lang="en">
<head>
<meta charset="utf-8">
<title>Sharpen Your Calling — Book Cover Wrap</title>
<link href="https://fonts.googleapis.com/css2?family=Ubuntu:ital,wght@0,300;0,400;1,300;1,400&display=swap" rel="stylesheet">
<style>
  :root{
    --paper:#ffffff;
    --ink:#1f1f1f;
    --body-grey:#6e6e6e;
    --title-grey:#727272;
    --orange:#f07a1f;
    --bullet:#f5a623;
    --spine-blue:#dbe9f8;
    --glass-light:#eef5fb;
    --glass-mid:#c9d6e2;
    --handle-yellow:#f6cf2c;
    --photo:#000000;
  }
  *{box-sizing:border-box;margin:0;padding:0}
  html,body{width:1200px;height:850px;overflow:hidden;background:var(--paper)}
  .cover{position:relative;width:1200px;height:850px;font-family:"Ubuntu",sans-serif;background:var(--paper);overflow:hidden}

  /* back cover */
  .back{position:absolute;left:0;top:0;width:552px;height:850px}
  .brand{position:absolute;left:120px;top:52px;display:flex;align-items:center;gap:12px}
  .brand-dot{width:44px;height:44px;border-radius:50%;background:var(--orange)}
  .brand-name{font-size:30px;font-weight:400;color:var(--orange);letter-spacing:.2px}
  .back-heading{position:absolute;left:47px;top:154px;font-size:16px;font-weight:400;color:var(--ink)}
  .back-copy{position:absolute;left:47px;top:180px;width:490px;font-size:10.4px;font-weight:300;line-height:24px;color:var(--body-grey)}
  .learn-heading{position:absolute;left:47px;top:370px;font-size:15.5px;font-weight:400;color:var(--ink)}
  .learn-list{position:absolute;left:47px;top:396px;list-style:none;font-size:10.4px;font-weight:300;line-height:24px;color:var(--body-grey)}
  .learn-list li{padding-left:12px;position:relative}
  .learn-list li::before{content:"•";position:absolute;left:0;color:var(--bullet)}
  .learn-close{margin-top:0;padding-left:0}
  .learn-close::before{content:none}
  .author-photo{position:absolute;left:47px;top:634px;width:164px;height:172px;background:var(--photo)}
  .bio{position:absolute;left:239px;top:635px;width:290px;font-size:10.4px;font-style:italic;font-weight:300;line-height:24px;color:var(--ink)}

  /* spine */
  .spine{position:absolute;left:552px;top:0;width:98px;height:850px;background:var(--spine-blue)}
  .spine-title{position:absolute;left:30px;top:30px;writing-mode:vertical-rl;white-space:nowrap}
  .spine-title .main{font-size:43px;font-weight:300;color:var(--title-grey);letter-spacing:1px}
  .spine-title .sub{font-size:27px;font-weight:300;color:var(--orange);letter-spacing:1px;margin-top:4px}
  .spine-author{position:absolute;left:36px;top:458px;writing-mode:vertical-rl;white-space:nowrap;font-size:24px;font-weight:300;color:var(--title-grey);letter-spacing:7px}
  .publisher{position:absolute;left:0;top:780px;width:98px;text-align:center}
  .publisher-dot{width:34px;height:34px;border-radius:50%;background:var(--ink);margin:0 auto 6px}
  .publisher-name{font-size:11.5px;font-weight:300;color:var(--ink);line-height:14px}

  /* front cover */
  .front{position:absolute;left:650px;top:0;width:550px;height:850px;background:linear-gradient(180deg,#ffffff 0%,#f7f7f7 60%,#ffffff 100%)}
  .front-title{position:absolute;left:0;top:4px;width:550px;text-align:center;line-height:1}
  .front-title .main{display:block;font-size:86px;font-weight:300;color:var(--title-grey);letter-spacing:2px;padding-left:56px}
  .front-title .sub{display:block;font-size:49px;font-weight:300;color:var(--orange);letter-spacing:2px;margin-top:8px;padding-left:50px}
  .hero-art{position:absolute;left:126px;top:164px;width:280px;height:596px}
  .front-author{position:absolute;left:0;top:792px;width:550px;text-align:center;padding-left:40px;font-size:35px;font-weight:300;color:var(--title-grey);letter-spacing:7px}
</style>
</head>
<body>
<div class="cover">

  <section class="back">
    <div class="brand">
      <span class="brand-dot"></span>
      <span class="brand-name">Quiet Harbor Wellness</span>
    </div>

    <h2 class="back-heading">Build a Mentoring Practice that Mirrors Your True Self</h2>
    <p class="back-copy">Do you want to step confidently into your new career by doing what you love? You aren't alone! But instead of doing what they love, many new coaches get stuck by trying to fit into traditional ways of doing business and create many unnecessary hurdles to happiness and success.<br>In this book, creative business coach, Norah Baltimer teaches you, as she has taught herself and many others, to stop feeling guilty about what you “should” do in your life and in the process you will learn how to turn your passion into a purposeful career.</p>

    <h3 class="learn-heading">New coaches will learn how to:</h3>
    <ul class="learn-list">
      <li>Recognize how your life decisions to this point are holding you back.</li>
      <li>Discover your gifts so you can express yourself through your creative projects.</li>
      <li>Identify and develop tools to bring your passion into purpose</li>
      <li>Offer services based on what you love to do.</li>
      <li>Understand your personal work style and work-flow to optimize your ideas and productivity.</li>
      <li>Create a message that reflects who you are to attract clients to work with you.</li>
      <li>Ask confidently for what you are worth and get it every time.</li>
      <li class="learn-close">Join Norah on the journey of reconnecting with yourself and manifesting your dream.</li>
    </ul>

    <div class="author-photo" role="img" aria-label="Author portrait of Norah Baltimer"></div>
    <p class="bio">Norah Baltimer, founder of Quiet Harbor Wellness, helps new coaches and creative entrepreneurs find their inner voice so that they have the confidence to bring their authentic selves out into the world. Norah has gone through this process for herself and helped other new businesses achieve dramatic improvements in their organi-zation and focus as a result.</p>
  </section>

  <section class="spine">
    <div class="spine-title"><span class="main">Sharpen</span><span class="sub">Your Calling</span></div>
    <div class="spine-author">Norah Baltimer</div>
    <div class="publisher">
      <div class="publisher-dot"></div>
      <div class="publisher-name">Lanternfield<br>Books</div>
    </div>
  </section>

  <section class="front">
    <h1 class="front-title"><span class="main">Sharpen</span><span class="sub">Your Calling</span></h1>
    <svg class="hero-art" viewBox="0 0 280 596" role="img" aria-label="Illustration of a silver magnifying glass with a yellow handle">
      <defs>
        <linearGradient id="heroTone" x1="0" y1="0" x2="0" y2="1">
          <stop offset="0" stop-color="var(--glass-light)"/>
          <stop offset=".45" stop-color="var(--glass-mid)"/>
          <stop offset=".6" stop-color="#e9d98a"/>
          <stop offset="1" stop-color="var(--handle-yellow)"/>
        </linearGradient>
      </defs>
      <rect x="0" y="0" width="280" height="596" rx="20" fill="url(#heroTone)" opacity=".85"/>
    </svg>
    <div class="front-author">Norah Baltimer</div>
  </section>

</div>
</body>
</html>
```